Chronicle of the Sage Oravel

We need a great book cover which honors the Name of the Sage Oravel. It should be classic clean and has islamic elements. It is a book in german language. I attached the informations which should be placed on the front- and backcover.

Target Market(s)

Islamic. Germany.

Font styles to use
Serif

Colors

Designer to choose colors to be used in the design.

Requirements
Must have
• Must include all texts i've attached in the pdfs.

```html
<!DOCTYPE html>
<html lang="de">
<head>
<meta charset="utf-8">
<title>Oravel – Buchumschlag</title>
<link rel="stylesheet" href="https://fonts.googleapis.com/css2?family=Noto+Serif:wght@400;600&family=Noto+Sans:wght@400&family=PT+Serif:ital@0;1&display=swap">
<style>
  :root{
    --page:#f1f1f1;
    --navy:#1b2a52;
    --navy-deep:#14213f;
    --teal-navy:#0d3a63;
    --gold-light:#f5e487;
    --gold:#d6a943;
    --gold-dark:#a8741f;
    --text-light:#e9edf5;
  }
  *{box-sizing:border-box;margin:0;padding:0}
  html,body{width:1200px;height:800px;overflow:hidden;background:var(--page)}
  .canvas{position:relative;width:1200px;height:800px}
  .cover{
    position:absolute;top:90px;width:420px;height:620px;overflow:hidden;
    background:linear-gradient(180deg,var(--navy) 0%,var(--teal-navy) 55%,var(--navy-deep) 100%);
    box-shadow:0 10px 30px rgba(0,0,0,.18);
  }
  .cover--back{left:150px}
  .cover--front{left:630px}
  .gold-band{
    position:absolute;top:0;bottom:0;width:30px;
    background:linear-gradient(180deg,var(--gold-dark) 0%,var(--gold-light) 22%,var(--gold) 45%,var(--gold-dark) 60%,var(--gold-light) 85%,var(--gold-light) 100%);
  }
  .gold-band--left{left:0}
  .gold-band--right{right:0}
  .pattern-field{position:absolute;inset:0 30px;
    background:radial-gradient(ellipse at 60% 20%,rgba(80,110,160,.35),transparent 60%)}
  /* front */
  .arch{position:absolute;left:30px;top:0;width:360px;height:620px}
  .calligraphy-mark{position:absolute;left:150px;top:168px;font-family:"Noto Serif",serif;font-size:40px;color:var(--gold)}
  .title{
    position:absolute;left:0;right:0;top:215px;text-align:center;
    font-family:"Noto Serif",serif;font-weight:600;font-size:54px;letter-spacing:3px;
    background:linear-gradient(180deg,var(--gold-light),var(--gold) 55%,var(--gold-dark));
    -webkit-background-clip:text;background-clip:text;color:transparent;
  }
  .rosette{position:absolute;right:34px;top:232px;width:36px;height:50px;border-radius:18px;
    background:linear-gradient(160deg,var(--gold-light),var(--gold-dark))}
  .subtitle{
    position:absolute;left:0;right:0;top:320px;text-align:center;
    font-family:"Noto Serif",serif;font-size:15px;line-height:1.45;letter-spacing:1px;color:var(--text-light)
  }
  .credits{
    position:absolute;left:0;right:0;top:418px;text-align:center;
    font-family:"Noto Sans",sans-serif;font-size:10.5px;line-height:1.7;letter-spacing:.8px;color:var(--text-light)
  }
  .credits .translator{font-style:italic}
  .publisher{
    position:absolute;left:0;right:0;bottom:60px;text-align:center;
    font-family:"Noto Serif",serif;font-size:15px;letter-spacing:1px;color:var(--text-light)
  }
  .publisher::before{content:"";display:block;width:10px;height:10px;margin:0 auto 8px;border:1px solid var(--text-light)}
  /* back */
  .blurb{
    position:absolute;left:58px;right:58px;top:140px;text-align:center;
    font-family:"PT Serif",serif;font-size:12.5px;line-height:1.6;color:var(--text-light)
  }
  .blurb em{font-style:italic}
</style>
</head>
<body>
<main class="canvas">

  <section class="cover cover--back" aria-label="Rückseite">
    <div class="pattern-field" role="img" aria-label="Dezentes geometrisches islamisches Muster"></div>
    <div class="gold-band gold-band--left"></div>
    <p class="blurb"><em>Al-Fuṣūl fī sīrat al-ḥakīm</em>, wörtlich „Die Kapitel über das Leben des Weisen“ ist eine kurze Zusammenfassung der Sira, die Biographie des Weisen Oravel. Sie enthält alles Wissenswerte über sein Leben und darüber hinaus einige Kapitel über seinen Alltag und seine Besonderheiten. Der Autor ordnet die Ereignisse der Sira ein. Diese unterscheiden sich je nach Auswertung der historischen Quellen. Der Autor Ibn Sareen heißt mit vollem Namen Halim ibn Sareen al-Tawfiq. Er ist um das Jahr 701 n. H. etwa 100 km südlich von Damaskus geboren. Seine Familie führte die Abstammung auf einen alten Stamm zurück. Sein Vater – ein bekannter Gelehrter – starb früh; der jüngste Sohn erinnert sich an ihn. Er wurde nach seinem ältesten Bruder benannt, zog nach Damaskus und lernte dort, wie sein Vater gehofft hatte, das Wissen zu studieren.</p>
    <div class="publisher">Lumen Verlag</div>
  </section>

  <section class="cover cover--front" aria-label="Vorderseite">
    <div class="pattern-field" role="img" aria-label="Dezentes geometrisches islamisches Muster"></div>
    <svg class="arch" viewBox="0 0 360 620" aria-hidden="true">
      <defs>
        <linearGradient id="archGold" x1="0" y1="0" x2="1" y2="1">
          <stop offset="0" stop-color="#f5e487"/>
          <stop offset=".5" stop-color="#d6a943"/>
          <stop offset="1" stop-color="#a8741f"/>
        </linearGradient>
      </defs>
      <path d="M45 620 V190 Q60 120 180 75 Q300 120 315 190 V620 Z" fill="#13234a" opacity=".55"/>
      <path d="M0 208 H18 Q40 110 180 42 Q315 110 330 200 H360" fill="none" stroke="url(#archGold)" stroke-width="6"/>
    </svg>
    <div class="gold-band gold-band--left"></div>
    <div class="gold-band gold-band--right"></div>
    <div class="calligraphy-mark">[</div>
    <h1 class="title">Oravel</h1>
    <div class="rosette" role="img" aria-label="Goldenes Rosettenornament"></div>
    <p class="subtitle">Seine Lebensgeschichte,<br>Fakten aus seinem Alltag<br>und seine Besonderheiten</p>
    <p class="credits">Von Halim ibn Sareen al-Tawfiq<br><span class="translator">Übersetzt und kommentiert von Jonas Wendelhof</span></p>
    <div class="publisher">Lumen Verlag</div>
  </section>

</main>
</body>
</html>
```